Professional, modern and unique business card. We are looking to present a new look to our business cards however we don't want to divert too far away from original template. We want social media links and our 3 office addresses on the backside of the business cards. Please see attached business card templates for ideas.
Crestline Homes Color Code:
R: 7
G:63
B:86

Target Market(s)

Real Estate

Industry/Entity Type

Real Estate

Contact Information for Business Card

Follow the attached templates. In need of a more modern and unique touch but don't want to divert from the original theme or color.
Crestline Homes Color Code:
R: 7
G:63
B:86

Font styles to use
Serif

Requirements
Must have
• Crestline Homes logo, Crestline homes colors, social media links, 3 office addresses,
Nice to have
• information about Crestline Homes and QR codes. You can check out www.mycrestlinehomes.example

```html
<!DOCTYPE html>
<html lang="en">
<head>
<meta charset="utf-8">
<title>Crestline Homes — Business Card</title>
<link rel="stylesheet" href="https://fonts.googleapis.com/css2?family=Lato:wght@400;700&display=swap">
<style>
  :root {
    --brand-navy: rgb(7, 63, 86);
    --card-text: #ffffff;
    --back-text: #dfe8ec;
    --disc-light: #f6f6f7;
    --disc-edge: #e4e2e4;
    --mark-blue: #a9d3df;
    --mark-faint: #c9dfe6;
    --social-dot: #6fa9c4;
    --stage: #eceff1;
  }
  * { margin: 0; padding: 0; box-sizing: border-box; }
  html, body { width: 1200px; height: 900px; overflow: hidden; }
  body {
    background: var(--stage);
    font-family: "Lato", Arial, sans-serif;
    position: relative;
  }
  .card {
    position: absolute;
    width: 620px;
    height: 384px;
    background: var(--brand-navy);
    box-shadow: 0 10px 28px rgba(0,0,0,0.18);
  }
  .card--front { left: 150px; top: 70px; }
  .card--back { left: 430px; top: 450px; }

  .disc {
    position: absolute;
    width: 334px;
    height: 334px;
    border-radius: 50%;
    background: radial-gradient(circle at 50% 40%, var(--disc-light) 0%, #f1eff1 60%, var(--disc-edge) 100%);
    box-shadow: inset 0 0 0 2px rgba(255,255,255,0.5), 0 2px 6px rgba(0,0,0,0.15);
    display: flex;
    align-items: center;
    justify-content: center;
  }
  .card--front .disc { left: 272px; top: 25px; }
  .card--back .disc { left: 15px; top: 25px; }

  .wordmark {
    font-family: "Lato", Arial, sans-serif;
    font-weight: 700;
    font-size: 34px;
    letter-spacing: 1px;
    color: var(--mark-blue);
    text-align: center;
  }
  .wordmark--faint { color: var(--mark-faint); }

  .identity { position: absolute; left: 35px; top: 42px; color: var(--card-text); }
  .identity__name { font-size: 28px; font-weight: 700; line-height: 1.05; letter-spacing: -0.3px; }
  .identity__title { font-size: 18px; font-weight: 400; line-height: 1.2; }

  .contact { position: absolute; left: 36px; top: 226px; list-style: none; color: var(--card-text); }
  .contact li { display: flex; align-items: center; font-size: 18px; line-height: 21.5px; }
  .contact svg { width: 15px; height: 15px; margin-right: 6px; fill: var(--card-text); }

  .back-info {
    position: absolute;
    right: 28px;
    top: 38px;
    text-align: right;
    color: var(--back-text);
    font-size: 18px;
    line-height: 21px;
  }
  .social-dots { display: flex; justify-content: flex-end; gap: 5px; margin-bottom: 6px; }
  .social-dots span { width: 24px; height: 24px; border-radius: 50%; background: var(--social-dot); }
  .handles { list-style: none; }
  .offices { margin-top: 16px; }
  .office { margin-bottom: 8px; }
</style>
</head>
<body>

<section class="card card--front">
  <div class="identity">
    <div class="identity__name">JORDAN HALE</div>
    <div class="identity__title">MANAGING DIRECTOR</div>
  </div>
  <ul class="contact">
    <li><svg viewBox="0 0 16 16"><path d="M2 6c0-2 3-3 6-3s6 1 6 3v1h-3V6H5v1H2z M4 8h8l1 5H3z"/></svg>212 555 0148</li>
    <li><svg viewBox="0 0 16 16"><path d="M4 1h8v14H4z M5.5 2.5v9h5v-9z M7 12.5h2v1H7z"/></svg>646 555 0172</li>
    <li><svg viewBox="0 0 16 16"><path d="M4 1h8v4H4z M1 6h14v6h-2v-2H3v2H1z M4 11h8v4H4z"/></svg>212 555 0199</li>
    <li><svg viewBox="0 0 16 16"><path d="M1 3h14v10H1z M2.5 4.5 8 9l5.5-4.5" stroke="rgb(7,63,86)" stroke-width="1.2"/></svg>info@crestlinehomes.example</li>
    <li><svg viewBox="0 0 16 16"><circle cx="8" cy="8" r="7"/><path d="M5 4l3 2-1 3 3 1-1 4" stroke="rgb(7,63,86)" stroke-width="1.4" fill="none"/></svg>www.crestlinehomes.example</li>
  </ul>
  <div class="disc">
    <div class="wordmark">Crestline Homes</div>
  </div>
</section>

<section class="card card--back">
  <div class="disc">
    <div class="wordmark wordmark--faint">Crestline Homes</div>
  </div>
  <div class="back-info">
    <div class="social-dots" role="img" aria-label="Social media links">
      <span></span><span></span><span></span><span></span><span></span><span></span>
    </div>
    <ul class="handles">
      <li>CrestlineHomesNY</li>
      <li>Info at Crestline Homes</li>
      <li>@CrestlineHomesNY</li>
      <li>Crestline Homes</li>
      <li>Crestline Homes New York</li>
      <li>@CrestlineHomesQ</li>
    </ul>
    <div class="offices">
      <div class="office">418-20 Harbor Blvd<br>Bayview, NY 11390</div>
      <div class="office">72-15 Linden Blvd<br>Elm Garden, NY 11432</div>
      <div class="office">1260 Orchard Ave<br>Westbrook, NY 11290</div>
    </div>
  </div>
</section>

</body>
</html>
```